Corvana Tongue Works, LLC

We need a business card that includes information about our business and conveys a reliable business that provides document translation services and interpreters for a variety of corporate and individual clients. We want to come across as professional, reliable, yet approachable. It should include the following on one side:

ESL / ENL Language Classes, Private Lessons, and Online Tutors
PLEXA Training and Testing
Translating & Interpreting Services
Contact us about Over-the-Phone Interpreting in over 200 languages
24/7/365
www.corvanatongue.example

The other side should include (555) 481-3062

Rhoda Pelling, President
482 Garnet Ave., Ste. 219
Indianapolis, IN 40917

Please add USA as part of the address. Also, please add rmpelling@corvanatongueworks.example as the e-mail address. Thank you.

Target Market(s)

Business professionals, their families, the international community

Industry/Entity Type

Business

Contact Information for Business Card

24/7/365
www.corvanatongue.example

(555) 481-3062

Rhoda Pelling, President
482 Garnet Ave., Ste. 219
Indianapolis, IN 40917
USA

Font styles to use
Sans Serif

Colors

Designer to choose colors to be used in the design.

Requirements
Must have
• See project description
• e-mail address and web address
• Phone number
Nice to have
• a globe
• physical address
Should not have
• Should not have the same color scheme as other agencies in our market in Indiana unless it is blue and black. No purple or yellow.

```html
<!DOCTYPE html>
<html lang="en">
<head>
<meta charset="utf-8">
<title>Corvana Tongue Works, LLC – Business Card</title>
<link href="https://fonts.googleapis.com/css2?family=Open+Sans:wght@500;600&family=Roboto:wght@400;500;700&display=swap" rel="stylesheet">
<style>
  :root {
    --page-bg: #2b2b2d;
    --card-bg: #ffffff;
    --brand-blue: #2a94d4;
    --ink: #111111;
    --map-tone: #eef0f2;
  }
  * { box-sizing: border-box; margin: 0; padding: 0; }
  html, body { width: 1189px; height: 1200px; overflow: hidden; }
  body {
    background: var(--page-bg);
    font-family: "Roboto", Arial, sans-serif;
    color: var(--ink);
    position: relative;
  }
  .card {
    position: absolute;
    left: 171px;
    width: 855px;
    height: 488px;
    background: var(--card-bg);
    border-radius: 48px;
    overflow: hidden;
  }
  .card--front { top: 67px; }
  .card--back { top: 625px; }

  .world-map {
    position: absolute;
    left: 60px; top: 90px;
    width: 730px; height: 330px;
    background: radial-gradient(ellipse at center, var(--map-tone) 0%, rgba(238,240,242,0.5) 55%, rgba(255,255,255,0) 75%);
  }

  .brand-mark {
    position: absolute;
    border-radius: 50%;
    background: var(--brand-blue);
    border: 4px solid #fff;
    box-shadow: 0 0 0 3px var(--brand-blue);
  }
  .brand-name {
    position: absolute;
    font-family: "Open Sans", Arial, sans-serif;
    font-weight: 500;
    color: var(--ink);
    line-height: 1.12;
    white-space: nowrap;
  }
  .card--front .brand-mark { left: 254px; top: 88px; width: 146px; height: 146px; }
  .card--front .brand-name { left: 410px; top: 100px; font-size: 39px; }
  .card--back .brand-mark { left: 75px; top: 178px; width: 128px; height: 128px; }
  .card--back .brand-name { left: 212px; top: 184px; font-size: 34px; }

  .services {
    position: absolute;
    left: 0; right: 0; top: 274px;
    text-align: center;
    font-size: 21px;
    line-height: 27px;
  }
  .front-web {
    position: absolute;
    left: 0; right: 0; top: 375px;
    text-align: center;
    font-size: 20px;
    letter-spacing: 4px;
  }
  .front-web .domain { color: var(--brand-blue); }
  .phone-band {
    position: absolute;
    left: 0; right: 0; top: 419px;
    height: 45px;
    background: var(--brand-blue);
    color: #fff;
    font-size: 20px;
    line-height: 45px;
    text-align: center;
  }

  .divider {
    position: absolute;
    left: 428px; top: 146px;
    width: 2px; height: 192px;
    background: var(--brand-blue);
  }
  .contact {
    position: absolute;
    left: 473px; top: 140px;
  }
  .contact__name { font-size: 25px; font-weight: 700; line-height: 30px; }
  .contact__title { font-size: 20px; color: var(--brand-blue); line-height: 22px; }
  .contact__address { margin-top: 22px; font-size: 21px; line-height: 27px; letter-spacing: 0.4px; }
  .contact__line {
    display: flex; align-items: center; gap: 10px;
    font-size: 21px; line-height: 29px;
  }
  .contact__line:first-of-type { margin-top: 9px; }
  .icon { width: 24px; height: 24px; flex: none; }
  .email {
    position: absolute;
    left: 0; right: 0; top: 410px;
    display: flex; justify-content: center; align-items: center; gap: 10px;
    font-size: 21px;
  }
</style>
</head>
<body>

<section class="card card--front">
  <div class="world-map" role="img" aria-label="Faint world map in light grey behind the logo and services"></div>
  <div class="brand-mark"></div>
  <div class="brand-name">Corvana<br>Tongue<br>Works LLC</div>
  <div class="services">
    <p>ESL / ENL Language Classes | Private Lessons and Online Tutors</p>
    <p>PLEXA Training and Testing</p>
    <p>Translating &amp; Interpreting Services</p>
  </div>
  <p class="front-web">www.<span class="domain">corvanatongue</span>.example</p>
  <p class="phone-band">Contact us about Over-the-Phone Interpreting in over 200 languages 24/7/365</p>
</section>

<section class="card card--back">
  <div class="brand-mark"></div>
  <div class="brand-name">Corvana<br>Tongue<br>Works LLC</div>
  <div class="divider"></div>
  <div class="contact">
    <p class="contact__name">Rhoda Pelling</p>
    <p class="contact__title">President</p>
    <p class="contact__address">482 Garnet Ave., Ste. 219<br>Indianapolis, IN 40917, USA</p>
    <p class="contact__line">
      <svg class="icon" viewBox="0 0 24 24" aria-hidden="true"><circle cx="12" cy="12" r="12" fill="#2a94d4"/><path d="M6 10c0-2 12-2 12 0v1h-3v-1H9v1H6z M8 12h8l1 5H7z" fill="#fff"/></svg>
      (555) 481-3062
    </p>
    <p class="contact__line">
      <svg class="icon" viewBox="0 0 24 24" aria-hidden="true"><circle cx="12" cy="12" r="12" fill="#2a94d4"/><g fill="none" stroke="#fff" stroke-width="1.2"><circle cx="12" cy="12" r="7"/><ellipse cx="12" cy="12" rx="3" ry="7"/><path d="M5 12h14M6 8.5h12M6 15.5h12"/></g></svg>
      www.corvanatongue.example
    </p>
  </div>
  <p class="email">
    <svg class="icon" viewBox="0 0 24 24" aria-hidden="true"><circle cx="12" cy="12" r="12" fill="#2a94d4"/><rect x="6" y="8" width="12" height="8.5" fill="none" stroke="#fff" stroke-width="1.3"/><path d="M6 8l6 5 6-5" fill="none" stroke="#fff" stroke-width="1.3"/></svg>
    rmpelling@corvanatongueworks.example
  </p>
</section>

</body>
</html>
```